Velmora Systems Website

Website design for our company: Velmora Systems.
The website should look fresh and IT focused. Please have a look at http://www.velmorasystems.example.au/ for our current design. We want something fresh and new, professional looking, in WordPress so we can easily make changes.

It Company

```html
<!DOCTYPE html>
<html lang="en">
<head>
<meta charset="utf-8">
<title>Velmora Systems</title>
<link href="https://fonts.googleapis.com/css2?family=Open+Sans:wght@400;600;700&display=swap" rel="stylesheet">
<style>
:root{
  --green:#17b55a;
  --green-deep:#0c4a25;
  --green-text:#19a04c;
  --link-green:#1f7a3c;
  --blue-title:#2f7fb8;
  --dark:#1c1c1c;
  --footer:#2e2e2e;
  --footer-bottom:#222;
  --text:#555;
  --muted:#777;
  --line:#d9d9d9;
}
*{margin:0;padding:0;box-sizing:border-box}
html,body{width:850px;height:1200px;overflow:hidden;background:#fff;font-family:"Open Sans",Arial,sans-serif;color:var(--text)}
.page{position:relative;width:850px;height:1200px}
.abs{position:absolute}

.site-header{left:0;top:0;width:850px;height:125px;background:linear-gradient(180deg,#2b2b2b,#151515)}
.brand{left:70px;top:16px;height:62px;display:flex;align-items:center;gap:10px}
.brand-mark{width:40px;height:40px;background:var(--green);border-radius:50%}
.brand-name{font-size:22px;font-weight:700;color:#fff}
.phone{right:73px;top:38px;text-align:right;color:#fff}
.phone small{display:block;font-size:12.5px;color:#ddd}
.phone strong{display:block;font-size:17px;font-weight:400;letter-spacing:.3px}

.main-nav{left:70px;top:89px;width:711px;height:36px;background:var(--green);display:flex}
.main-nav a{color:#fff;text-decoration:none;font-size:11px;font-weight:700;display:flex;align-items:center;justify-content:center;border-right:1px solid #13954a}
.main-nav a:last-child{border-right:none}

.hero{left:70px;top:125px;width:711px;height:285px;background:linear-gradient(180deg,#f2f2f2 0%,#d8d8d8 45%,#3a3a3a 60%,#e4e4e4 100%);border:1px solid #ddd}
.hero-caption{left:70px;top:216px;width:355px;height:117px;background:rgba(40,40,40,.82);padding:14px 22px}
.hero-caption h1{font-size:26px;font-weight:400;color:var(--green);line-height:1.15}
.hero-caption h2{font-size:19px;font-weight:400;color:#fff;margin-top:2px}
.hero-caption p{font-size:8.5px;color:#bbb;line-height:1.6;margin-top:5px}
.dots{left:402px;top:390px;display:flex;gap:4px}
.dots span{width:10px;height:10px;border-radius:50%;background:#333}

.service{top:426px;width:172px}
.service .thumb{height:79px}
.service h3{font-size:13.5px;font-weight:400;color:var(--blue-title);margin-top:8px}
.service p{font-size:9px;line-height:15.5px;color:var(--muted);margin-top:2px}
.service a{font-size:10px;font-weight:600;color:var(--link-green);text-decoration:none;display:block;margin-top:1px}

.welcome{left:70px;top:644px;width:480px}
.welcome h2{font-size:20px;font-weight:400;color:var(--green-text)}
.welcome .lead{font-size:10.5px;line-height:15.5px;margin-top:9px;color:#555}
.welcome p{font-size:9px;line-height:15.5px;margin-top:7px;color:#666}

.quick{left:588px;top:638px;width:193px;height:157px;border:1px solid var(--line)}
.quick h3{height:34px;background:#f3f3f3;border-bottom:1px solid var(--line);font-size:14.5px;font-weight:400;color:#333;padding:6px 18px}
.quick .field{margin:12px 14px 0;height:24px;border:1px solid #ccc;border-radius:2px;font-size:8.5px;color:#888;padding:5px 9px}
.quick .field + .field{margin-top:8px}
.quick .btn{margin:11px 12px 0 14px;height:30px;border-radius:3px;background:linear-gradient(180deg,#16603a,var(--green-deep));color:#fff;font-size:13px;display:flex;align-items:center;justify-content:center}

.partners{left:70px;top:876px;width:711px;height:40px;display:flex;justify-content:space-between;align-items:center}
.partners span{font-size:19px;font-weight:700}

.site-footer{left:0;top:952px;width:850px;height:198px;background:var(--footer)}
.fcol{top:983px;color:#ddd}
.fcol h4{font-size:12.5px;font-weight:600;color:#fff;margin-bottom:6px}
.fcol li{list-style:none;font-size:9px;line-height:17.4px;color:#ddd}
.bottom-bar{left:0;top:1150px;width:850px;height:50px;background:var(--footer-bottom);border-top:1px solid #3a3a3a}
.copy{left:60px;top:1166px;font-size:8.5px;color:#ddd}
.social{left:685px;top:1164px;display:flex;gap:6px}
.social span{width:14px;height:14px;background:#6b8cae;border-radius:2px}
.social span:last-child{background:#e8782a}
</style>
</head>
<body>
<div class="page">
  <header class="site-header abs"></header>
  <div class="brand abs"><span class="brand-mark"></span><span class="brand-name">Velmora Systems</span></div>
  <div class="phone abs"><small>Phone Support</small><strong>555.0143.2760</strong></div>
  <nav class="main-nav abs">
    <a style="width:79px">HOME</a><a style="width:102px">ABOUT US</a><a style="width:88px">CLIENTS</a><a style="width:97px">SERVICES</a><a style="width:101px">SUPPORTS</a><a style="width:120px">TESTIMONIALS</a><a style="width:124px">CONTACT US</a>
  </nav>

  <div class="hero abs" role="img" aria-label="Photo of a bright data centre with rows of server racks"></div>
  <div class="hero-caption abs">
    <h1>Computer and IT Services</h1>
    <h2>Aliquam erat purus cursus</h2>
    <p>Etiam eu urna Sed porta Suspendisse quam leo molestie sed<br>luctus quis feugiat in pede Fusce tellus Sed metus</p>
  </div>
  <div class="dots abs"><span></span><span></span><span></span><span></span></div>

  <div class="service abs" style="left:69px">
    <div class="thumb" role="img" aria-label="Photo of a support technician with a headset" style="background:linear-gradient(135deg,#c99a5a,#6b4a2a)"></div>
    <h3>On-site Service</h3><p>Pellentesque faucibus Ut accumsan ultricies elit Maecenas at justo</p><a>Read More</a>
  </div>
  <div class="service abs" style="left:247px">
    <div class="thumb" role="img" aria-label="Photo of a remote support agent at a computer" style="background:linear-gradient(135deg,#eeeeee,#8a8f96)"></div>
    <h3>Remote Desktop Support</h3><p>Pellentesque faucibus Ut accumsan ultricies elit Maecenas at justo</p><a>Read More</a>
  </div>
  <div class="service abs" style="left:429px">
    <div class="thumb" role="img" aria-label="Photo of technicians working in a server room" style="background:linear-gradient(135deg,#8fa7a0,#3f5450)"></div>
    <h3>Medical IT Service</h3><p>Pellentesque faucibus Ut accumsan ultricies elit Maecenas at justo</p><a>Read More</a>
  </div>
  <div class="service abs" style="left:605px">
    <div class="thumb" role="img" aria-label="Photo of an office team with a headset operator" style="background:linear-gradient(135deg,#d6dde6,#7d8a99)"></div>
    <h3>Pharmacy IT Service</h3><p>Pellentesque faucibus Ut accumsan ultricies elit Maecenas at justo</p><a>Read More</a>
  </div>

  <section class="welcome abs">
    <h2>Welcome to Velmora Systems Mainpage</h2>
    <p class="lead">Velmora Systems is an Adelaide based company with a single objective - to excel in the support and service of all computer and IT needs.</p>
    <p>We provide a high level of consulting services using the most experienced engineers at a reasonable and fair price. We believe in using a Business Value approach to every aspect of computer consulting to provide our clients with the most cost effective solutions.</p>
    <p>We strongly believe that we are in business with our clients. Each thing we do must be measured against our clients' business objectives. At the end of the day our client's success is our success.</p>
  </section>

  <aside class="quick abs">
    <h3>Quick Support</h3>
    <div class="field">Type name</div>
    <div class="field">Type your digit</div>
    <div class="btn">Start Now</div>
  </aside>

  <div class="partners abs">
    <span style="color:#7b8aa8">Northvane</span>
    <span style="color:#111">Calderon</span>
    <span style="color:#c0392b">Pyxiscore</span>
    <span style="color:#1d63a8">Helmcrest</span>
    <span style="color:#1b6fb0">Oridian</span>
    <span style="color:#1a6a66">Quellis</span>
  </div>

  <footer class="site-footer abs"></footer>
  <div class="fcol abs" style="left:69px"><h4>COMPANY</h4><ul><li>About Us</li><li>Services</li><li>Solutions</li><li>Case Studies</li><li>Awards</li></ul></div>
  <div class="fcol abs" style="left:202px"><h4>FEATURES</h4><ul><li>Sed porta</li><li>Suspendisse quam</li><li>Leo molestie</li><li>Sed luctus quis</li><li>Tempor cursus</li></ul></div>
  <div class="fcol abs" style="left:349px"><h4>SERVICES</h4><ul><li>Phasellus felis dolor</li><li>Scelerisque tempus</li><li>Eget lobortis</li><li>Libero Aliquam</li></ul></div>
  <div class="fcol abs" style="left:495px"><h4>SUPPORT</h4><ul><li>Sed porta</li><li>Suspendisse quam</li><li>Leo molestie</li><li>Sed luctus quis</li></ul></div>
  <div class="fcol abs" style="left:627px"><h4>CONTACT</h4><ul><li>48 Larkfield Ave, Suite 210</li><li>Adelaide, SA 5000</li><li>Tel: +61 (0)8 5550 1294</li><li>hello@velmorasystems.example.au</li></ul></div>

  <div class="bottom-bar abs"></div>
  <div class="copy abs">© 2014 Velmora Systems.&nbsp; All right reserved.&nbsp; Term of Use</div>
  <div class="social abs"><span></span><span></span><span></span><span></span></div>
</div>
</body>
</html>
```